Home Security Company Business Card

Looking for a eye catching business card that is non traditional and stands out but yet still looks professional. It should include all the pertinent information such as name, title, address, telephone, e-mail, website address should definitely stand out and then finally the logo.

Target Market(s)

Residential and Commercial accounts mostly upscale accounts

Industry/Entity Type

Security

Contact Information for Business Card

Name
Title
Address
Office #
Cell #
E-mail
Website

Font styles to use
Serif
Sans Serif

Requirements
Must have
• Logo, two sided color configuration
Nice to have
• You decide
Should not have
• There really aren't any.

```html
<!DOCTYPE html>
<html lang="en">
<head>
<meta charset="utf-8">
<title>Bastion Home Protection – Business Card</title>
<link rel="stylesheet" href="https://fonts.googleapis.com/css2?family=Arimo:wght@400;700&display=swap">
<style>
  :root {
    --backdrop: #4a413c;
    --card: #1b1b1c;
    --card-edge: #262627;
    --silver: #b9b9bb;
    --silver-dim: #8d8d90;
    --crimson: #b3241a;
    --gold: #d89a2a;
    --ink-light: #ededed;
    --divider: #6a6a6c;
  }
  * { box-sizing: border-box; margin: 0; padding: 0; }
  html, body {
    width: 1200px; height: 787px; overflow: hidden;
    background: var(--backdrop);
    font-family: "Arimo", Arial, sans-serif;
  }
  .canvas {
    position: relative; width: 1200px; height: 787px;
    display: flex; align-items: center; justify-content: center; gap: 44px;
  }
  .card {
    position: relative; width: 540px; height: 309px;
    background: var(--card);
    border: 1px solid var(--card-edge);
    box-shadow: 0 10px 30px rgba(0,0,0,.35);
  }

  /* Front side */
  .card-front {
    display: flex; flex-direction: column; align-items: center; justify-content: center;
  }
  .brand {
    display: flex; align-items: center; gap: 12px;
  }
  .brand-dot {
    width: 18px; height: 18px; border-radius: 50%;
  }
  .brand-name {
    font-weight: 700; letter-spacing: .5px; line-height: 1.15;
  }
  .card-front .brand-dot { background: var(--silver); }
  .card-front .brand-name { color: var(--silver); font-size: 26px; }
  .front-web {
    margin-top: 42px; color: var(--silver-dim);
    font-size: 14px; letter-spacing: 3px;
  }

  /* Back side */
  .card-back { display: flex; align-items: center; }
  .back-brand {
    width: 292px; padding-left: 34px;
  }
  .card-back .brand-dot { background: var(--crimson); width: 16px; height: 16px; }
  .card-back .brand-name { color: var(--crimson); font-size: 19px; }
  .divider {
    width: 1px; height: 176px;
    background: linear-gradient(to bottom, transparent, var(--divider) 20%, var(--divider) 80%, transparent);
  }
  .contact { padding-left: 20px; color: var(--ink-light); font-size: 14px; line-height: 1.45; }
  .person-name { color: var(--crimson); font-size: 18px; font-weight: 700; }
  .person-title { color: var(--gold); font-size: 14px; font-weight: 700; margin-bottom: 6px; }
  .address { margin-bottom: 2px; }
  .contact-line { display: flex; align-items: center; gap: 8px; }
  .contact-line svg { width: 13px; height: 13px; fill: var(--crimson); flex: none; }
  .web-line { margin-top: 4px; }
</style>
</head>
<body>
<main class="canvas">

  <section class="card card-front" aria-label="Card front">
    <div class="brand">
      <span class="brand-dot"></span>
      <span class="brand-name">BASTION<br>HOME PROTECTION INC.</span>
    </div>
    <p class="front-web">www.bastionhome.com</p>
  </section>

  <section class="card card-back" aria-label="Card back">
    <div class="back-brand">
      <div class="brand">
        <span class="brand-dot"></span>
        <span class="brand-name">BASTION<br>HOME PROTECTION INC.</span>
      </div>
    </div>
    <div class="divider"></div>
    <div class="contact">
      <p class="person-name">Mark Ellison</p>
      <p class="person-title">President</p>
      <p class="address">2471 Harrow Lane<br>Brookfield, CT 06804</p>
      <p class="contact-line">
        <svg viewBox="0 0 16 16" aria-hidden="true"><path d="M3.6 1.2l2.3 2.6-1.3 1.9c.9 2 2.6 3.7 4.6 4.6l1.9-1.3 2.6 2.3-1.2 2.2C7 13.2 2.8 9 1.4 2.4z"/></svg>
        555 0142 7781
      </p>
      <p class="contact-line">
        <svg viewBox="0 0 16 16" aria-hidden="true"><path d="M4.5 0h7a1 1 0 0 1 1 1v14a1 1 0 0 1-1 1h-7a1 1 0 0 1-1-1V1a1 1 0 0 1 1-1zm.6 2v10h5.8V2zM8 13a1 1 0 1 0 0 2 1 1 0 0 0 0-2z"/></svg>
        555 0198 3346
      </p>
      <p class="contact-line">
        <svg viewBox="0 0 16 16" aria-hidden="true"><path d="M1 3h14v10H1zm1.4 1.3L8 8.6l5.6-4.3z"/></svg>
        mark@bastionhome.com
      </p>
      <p class="contact-line web-line">
        <svg viewBox="0 0 16 16" aria-hidden="true"><path d="M8 0a5.5 5.5 0 0 0-5.5 5.5C2.5 10 8 16 8 16s5.5-6 5.5-10.5A5.5 5.5 0 0 0 8 0zm0 8a2.5 2.5 0 1 1 0-5 2.5 2.5 0 0 1 0 5z"/></svg>
        www.bastionhome.com
      </p>
    </div>
  </section>

</main>
</body>
</html>
```